Velutra Showcases | Web Design Project

We need a web design for a new Promotion Company based in Toronto, Canada named Velutra Showcases.

Velutra Showcases has an idea and vision to set high standard, be EXCLUSIVE and attract a group of people that will follow us through events we promote (night clubs, brand promotions, music events, and sport events)

We want to present a high standards and classy image to the others...

layout/style of the website would be best explained by this template

http://www.gorvikdesigns.example/view-ttemplate-58174.html

Target Market(s)

male/female age 25-40 Target: business owners young entrepreneur - clubing industry - media industry - promotion industry - marketing media industry

Industry/Entity Type

It Company

Requirements
Must have
• website would have about 5 pages ... example in terms of content (http://www.brastonhouse.example/lifestyle.html)

About Velutra
Events
Media
Promotions
Affiliates
Contact

as well as twitter and facebook logo/links
newsletter section
music control

need to have a easy to view gallery page (pictures from events)
Events would have to include flyers .. for past/future events
Media - would include videos/pictures from the events

Affiliates - list of affiliates with their logos and short description..

Main Pages
background would be pictures of Toronto
it would be nice to have some kind of flash/swf
space for flyer and picture of the week...

logo file is uploaded.

```html
<!DOCTYPE html>
<html lang="en">
<head>
<meta charset="utf-8">
<title>Velutra Showcases</title>
<link rel="stylesheet" href="https://fonts.googleapis.com/css2?family=Fira+Sans+Condensed:ital,wght@0,400;1,400;1,600&family=PT+Sans:wght@400&display=swap">
<style>
  :root {
    --ink: #000000;
    --night: #03080c;
    --teal: #1ab0cc;
    --cyan: #27c4e8;
    --frame: #17879e;
    --text: #ffffff;
    --button-top: #5fd0f5;
    --button-bottom: #1a8fd0;
    --button-ink: #06243a;
    --social-a-top: #6aa8e0;
    --social-a-bottom: #2a60a8;
    --social-b-top: #8ad8f0;
    --social-b-bottom: #3a9ad0;
    --sound-on: #f0a020;
    --sound-off: #e02010;
  }
  * { margin: 0; padding: 0; box-sizing: border-box; }
  html, body { width: 1200px; height: 917px; overflow: hidden; background: var(--ink); }
  .page {
    position: relative; width: 1200px; height: 917px; overflow: hidden;
    background: var(--ink); color: var(--text);
    font-family: "PT Sans", sans-serif;
  }

  /* Top navigation */
  .top-bar { position: absolute; left: 0; top: 0; width: 1200px; height: 82px; background: var(--night); }
  .spot {
    position: absolute; top: 0; width: 110px; height: 36px; transform: translateX(-50%);
    background: radial-gradient(ellipse 50% 60% at 50% 20%, rgba(39,196,232,.85), rgba(39,196,232,.15) 55%, transparent 75%);
  }
  .main-nav a {
    position: absolute; top: 34px; transform: translateX(-50%);
    font-family: "Fira Sans Condensed", sans-serif; font-style: italic;
    font-size: 20px; color: var(--text); text-decoration: none; white-space: nowrap;
  }
  .main-nav .current {
    left: 90px; top: 33px; width: 154px; height: 30px; transform: none;
    border: 1px solid var(--frame); text-align: center; line-height: 28px;
    background: #0a1a20;
  }
  .sub-nav { position: absolute; left: 90px; top: 63px; width: 154px; z-index: 3; list-style: none; }
  .sub-nav li {
    height: 29px; border: 1px solid var(--frame); border-top: none;
    background: #04141a; font-size: 16px; line-height: 28px; padding-left: 30px; position: relative;
  }
  .sub-nav li::before {
    content: ""; position: absolute; left: 13px; top: 9px;
    border-left: 8px solid var(--cyan); border-top: 5px solid transparent; border-bottom: 5px solid transparent;
  }

  /* Header band */
  .header-band {
    position: absolute; left: 0; top: 82px; width: 1200px; height: 108px;
    background: linear-gradient(90deg, #0d5a6e 0%, #062a35 18%, #020b0f 45%, #03141a 70%, #0b5e74 100%);
    border-top: 1px solid #1a6d80; border-bottom: 1px solid #1a6d80;
  }
  .brand {
    position: absolute; right: 16px; top: 22px; text-align: right;
    font-family: "PT Sans", sans-serif; font-size: 62px; line-height: 58px;
    letter-spacing: 4px; color: var(--cyan); text-transform: uppercase;
  }
  .brand small { display: block; font-size: 20px; line-height: 24px; letter-spacing: 11px; color: var(--cyan); }

  /* Background scene */
  .backdrop {
    position: absolute; left: 0; top: 191px; width: 1200px; height: 681px;
    background:
      radial-gradient(ellipse 120px 330px at 820px 360px, rgba(60,200,230,.45), transparent 70%),
      radial-gradient(ellipse 260px 200px at 1000px 560px, rgba(120,90,40,.25), transparent 70%),
      linear-gradient(180deg, #000 0%, #03080c 55%, #0b1418 85%, #05080a 100%);
  }

  /* Gallery */
  .gallery {
    position: absolute; left: 24px; top: 228px; width: 620px; height: 614px;
    border: 1px solid var(--frame); background: rgba(0,0,0,.55);
  }
  .gallery-main {
    position: absolute; left: 2px; top: 2px; width: 614px; height: 474px;
    background:
      radial-gradient(ellipse 140px 160px at 220px 180px, rgba(240,250,255,.9), rgba(70,160,190,.4) 55%, transparent 80%),
      linear-gradient(180deg, #061a2a 0%, #0e3a50 45%, #5a6a50 70%, #2a2a24 100%);
  }
  .thumbs { position: absolute; left: 15px; top: 492px; display: flex; gap: 10px; }
  .thumb { width: 110px; height: 98px; border: 1px solid #e8e8e8; }
  .thumb-1 { background: linear-gradient(180deg, #0a2a3a, #6a8a90 50%, #2a2a24); }
  .thumb-2 { background: linear-gradient(160deg, #3a2a34, #8a6a80 55%, #2a2026); }
  .thumb-3 { background: linear-gradient(180deg, #0a0a14, #b8a888 55%, #14100c); }
  .thumb-4 { background: linear-gradient(180deg, #6aa0d0, #c8d4dc 55%, #1a4a60); }
  .thumb-5 { background: linear-gradient(180deg, #2a50a0, #5a80c0 55%, #c06a3a 80%, #1a2030); }

  /* About copy */
  .about { position: absolute; left: 678px; top: 240px; width: 498px; }
  .about h1 {
    font-family: "Fira Sans Condensed", sans-serif; font-style: italic; font-weight: 600;
    font-size: 28px; line-height: 34px; color: var(--cyan); text-decoration: underline; text-underline-offset: 3px;
    margin-bottom: 16px;
  }
  .about p { font-size: 13.8px; line-height: 21.6px; color: var(--text); margin-bottom: 43px; }
  .cta {
    position: absolute; left: 1058px; top: 592px; width: 100px; height: 27px;
    border-radius: 14px; background: linear-gradient(180deg, var(--button-top), var(--button-bottom));
    color: var(--button-ink); font-size: 16px; line-height: 27px; text-align: center; text-decoration: none;
  }

  /* Footer */
  .footer {
    position: absolute; left: 0; top: 872px; width: 1200px; height: 45px; background: var(--teal);
    font-family: "Fira Sans Condensed", sans-serif; font-style: italic; font-size: 13px; color: var(--text);
  }
  .copyright { position: absolute; left: 48px; top: 14px; }
  .sound { position: absolute; left: 901px; top: 13px; display: flex; align-items: center; gap: 8px; font-weight: 600; }
  .sound svg { margin-left: 8px; }
  .social { position: absolute; left: 1083px; top: 7px; display: flex; gap: 9px; }
  .social a { width: 30px; height: 30px; border-radius: 4px; display: block; }
  .social-first { background: linear-gradient(180deg, var(--social-a-top), var(--social-a-bottom)); }
  .social-second { background: linear-gradient(180deg, var(--social-b-top), var(--social-b-bottom)); }
</style>
</head>
<body>
<div class="page">
  <header class="top-bar">
    <span class="spot" style="left:156px"></span>
    <span class="spot" style="left:342px"></span>
    <span class="spot" style="left:504px"></span>
    <span class="spot" style="left:686px"></span>
    <span class="spot" style="left:890px"></span>
    <span class="spot" style="left:1080px"></span>
    <nav class="main-nav">
      <a class="current" href="#">About Velutra</a>
      <a href="#" style="left:340px">Events</a>
      <a href="#" style="left:504px">Media</a>
      <a href="#" style="left:692px">Promotions</a>
      <a href="#" style="left:898px">Affiliates</a>
      <a href="#" style="left:1081px">Contact</a>
    </nav>
  </header>
  <ul class="sub-nav">
    <li>Link1</li><li>Link2</li><li>Link3</li><li>Link4</li>
  </ul>

  <div class="header-band">
    <div class="brand">Velutra<small>Showcases</small></div>
  </div>

  <div class="backdrop" role="img" aria-label="Night view of tall curved city towers lit in blue"></div>

  <section class="gallery">
    <div class="gallery-main" role="img" aria-label="Busy public square at night with crowds, fountains and lit towers"></div>
    <div class="thumbs">
      <div class="thumb thumb-1" role="img" aria-label="Public square at night"></div>
      <div class="thumb thumb-2" role="img" aria-label="Aerial view of a highway interchange"></div>
      <div class="thumb thumb-3" role="img" aria-label="Waterfront concert hall at night"></div>
      <div class="thumb thumb-4" role="img" aria-label="Curved office towers by day"></div>
      <div class="thumb thumb-5" role="img" aria-label="City skyline at dusk over a lake"></div>
    </div>
  </section>

  <section class="about">
    <h1>About Us</h1>
    <p>Lorem Ipsum is simply dummy text of the printing and typesetting industry. Lorem Ipsum has been the industry's standard dummy text ever since the 1500s, when an unknown printer took a galley of type and scrambled it to make a type specimen book</p>
    <p>It is a long established fact that a reader will be distracted by the readable content of a page when looking at its layout. The point of using Lorem Ipsum is that it has a more-or-less normal distribution of letters, as opposed to using 'Content here, content here', making it look like readable English. Many desktop publishing packages and web page editors now use Lorem Ipsum as their default model text, and a search for 'lorem ipsum' will uncover many web sites still in their infancy. Various versions have evolved over the years, sometimes by accident, sometimes on purpose (injected humour and the like).</p>
  </section>
  <a class="cta" href="#">Click here</a>

  <footer class="footer">
    <span class="copyright">Copyright (c) 2011. www.velutra.example</span>
    <div class="sound">
      <span>Sound</span>
      <svg width="9" height="9" viewBox="0 0 9 9"><circle cx="4.5" cy="4.5" r="4" fill="var(--sound-on)"/></svg><span>On</span>
      <svg width="9" height="9" viewBox="0 0 9 9"><circle cx="4.5" cy="4.5" r="4" fill="var(--sound-off)"/></svg><span>Off</span>
    </div>
    <div class="social">
      <a class="social-first" href="#" aria-label="Social profile"></a>
      <a class="social-second" href="#" aria-label="Social feed"></a>
    </div>
  </footer>
</div>
</body>
</html>
```